Home Security Company Business Card

Looking for a eye catching business card that is non traditional and stands out but yet still looks professional. It should include all the pertinent information such as name, title, address, telephone, e-mail, website address should definitely stand out and then finally the logo.

Target Market(s)

Residential and Commercial accounts mostly upscale accounts

Industry/Entity Type

Security

Contact Information for Business Card

Name
Title
Address
Office #
Cell #
E-mail
Website

Font styles to use
Serif
Sans Serif

Requirements
Must have
• Logo, two sided color configuration
Nice to have
• You decide
Should not have
• There really aren't any.

```html
<!DOCTYPE html>
<html lang="en">
<head>
<meta charset="utf-8">
<title>Wardline Security Systems – Business Card</title>
<link rel="stylesheet" href="https://fonts.googleapis.com/css2?family=Open+Sans:wght@400;600&display=swap">
<style>
  :root {
    --backdrop: #e9e7e5;
    --card: #f8f7f6;
    --card-edge: #ffffff;
    --maroon: #7a1d12;
    --gold: #e2a23c;
    --ink: #3b3b3b;
    --icon: #7a1d12;
  }
  * { margin: 0; padding: 0; box-sizing: border-box; }
  html, body {
    width: 1200px;
    height: 900px;
    overflow: hidden;
    background: var(--backdrop);
    font-family: "Open Sans", Arial, sans-serif;
  }
  .canvas {
    position: relative;
    width: 1200px;
    height: 900px;
    display: flex;
    align-items: center;
    justify-content: center;
  }
  .business-card {
    position: relative;
    width: 960px;
    height: 590px;
    background: var(--card);
    border: 3px solid var(--card-edge);
    border-radius: 26px;
    box-shadow: 0 14px 40px rgba(0, 0, 0, 0.12);
  }
  .brand {
    position: absolute;
    left: 70px;
    top: 90px;
    width: 330px;
    display: flex;
    flex-direction: column;
    align-items: center;
    gap: 34px;
  }
  .brand-mark {
    width: 170px;
    height: 170px;
    border-radius: 50%;
    background: var(--maroon);
  }
  .brand-name {
    color: var(--maroon);
    font-weight: 600;
    font-size: 34px;
    line-height: 1.2;
    text-align: center;
  }
  .details {
    position: absolute;
    left: 504px;
    top: 100px;
    color: var(--ink);
  }
  .person-name {
    color: var(--maroon);
    font-weight: 600;
    font-size: 36px;
    line-height: 1.2;
  }
  .person-title {
    color: var(--gold);
    font-size: 24px;
    margin-top: 4px;
  }
  .address {
    font-style: normal;
    font-size: 24px;
    line-height: 33px;
    margin-top: 30px;
  }
  .contact-list {
    list-style: none;
    margin-top: 36px;
    font-size: 24px;
    line-height: 35px;
  }
  .contact-list li {
    display: flex;
    align-items: center;
    gap: 14px;
  }
  .contact-list svg {
    width: 18px;
    height: 18px;
    fill: var(--icon);
    flex: none;
  }
</style>
</head>
<body>
<main class="canvas">
  <section class="business-card">
    <div class="brand">
      <div class="brand-mark"></div>
      <div class="brand-name">Wardline Security Systems Inc.</div>
    </div>

    <div class="details">
      <h1 class="person-name">Daniel Hartley</h1>
      <p class="person-title">Managing Director</p>

      <address class="address">
        1234, Address Goes Here<br>
        Country Name, 123456
      </address>

      <ul class="contact-list">
        <li>
          <svg viewBox="0 0 18 18" aria-hidden="true"><path d="M5 1h8a1 1 0 0 1 1 1v14a1 1 0 0 1-1 1H5a1 1 0 0 1-1-1V2a1 1 0 0 1 1-1zm1 2v10h6V3zm3 11a1 1 0 1 0 0 2 1 1 0 0 0 0-2z"/></svg>
          <span>123-456-7890</span>
        </li>
        <li>
          <svg viewBox="0 0 18 18" aria-hidden="true"><path d="M1 6c2-3 14-3 16 0l-1 2-3-1V5H5v2L2 8zM4 9l2-2h6l2 2 1 6H3zm5 1a2 2 0 1 0 0 4 2 2 0 0 0 0-4z"/></svg>
          <span>123-456-7890</span>
        </li>
        <li>
          <svg viewBox="0 0 18 18" aria-hidden="true"><path d="M1 4h16v10H1zm2 1.5 6 4.5 6-4.5V5H3z"/></svg>
          <span>info@youremail.com</span>
        </li>
        <li>
          <svg viewBox="0 0 18 18" aria-hidden="true"><path d="M7.5 10.5l3-3M6 8 3.5 10.5a2.5 2.5 0 0 0 3.5 3.5L9.5 11.5M12 10l2.5-2.5A2.5 2.5 0 0 0 11 4L8.5 6.5" fill="none" stroke="#7a1d12" stroke-width="1.8" stroke-linecap="round"/></svg>
          <span>www.yourweb.com</span>
        </li>
      </ul>
    </div>
  </section>
</main>
</body>
</html>
```